Veldmark Supplies Business Card

Professional business card that stand out to our potential customers. Front and back with clean modern design

Industry/Entity Type

Oil and gas

Contact Information for Business Card

Name, address, website , office phone and cell number

Requirements
Must have
• Editable files for each employee

```html
<!DOCTYPE html>
<html lang="en">
<head>
<meta charset="utf-8">
<title>Veldmark Supplies Business Card</title>
<link rel="stylesheet" href="https://fonts.googleapis.com/css2?family=Arimo:wght@400;700&display=swap">
<style>
  :root {
    --stage: #3b3b3b;
    --card-dark: #262626;
    --card-dark-text: #3d3d3d;
    --card-light: #ffffff;
    --brand-red: #ff0000;
    --brand-blue: #1aa8c8;
    --white: #ffffff;
  }
  * { margin: 0; padding: 0; box-sizing: border-box; }
  html, body { width: 1200px; height: 689px; overflow: hidden; }
  body {
    background: var(--stage);
    font-family: "Arimo", Arial, sans-serif;
    position: relative;
  }
  .card {
    position: absolute;
    top: 196px;
    width: 520px;
    height: 297px;
    border-radius: 16px;
    overflow: hidden;
  }
  .card-back { left: 53px; background: var(--card-dark); }
  .card-front { left: 627px; background: var(--card-light); }

  .back-wordmark {
    position: absolute;
    inset: 0;
    display: flex;
    align-items: center;
    justify-content: center;
    gap: 12px;
  }
  .back-wordmark .mark-square {
    width: 26px; height: 26px;
    background: var(--card-dark-text);
  }
  .back-wordmark .company-name {
    color: var(--card-dark-text);
    font-weight: 700;
    font-size: 30px;
    letter-spacing: 1px;
    text-transform: uppercase;
  }

  .front-bands { position: absolute; inset: 0; }

  .front-wordmark {
    position: absolute;
    left: 26px;
    top: 112px;
    display: flex;
    align-items: center;
    gap: 8px;
  }
  .front-wordmark .mark-square {
    width: 18px; height: 18px;
    background: var(--brand-red);
  }
  .front-wordmark .company-name {
    color: var(--brand-red);
    font-weight: 700;
    font-size: 20px;
    text-transform: uppercase;
    letter-spacing: 0.5px;
  }

  .holder {
    position: absolute;
    right: 34px;
    top: 26px;
    text-align: right;
  }
  .holder-name {
    color: var(--brand-red);
    font-weight: 700;
    font-size: 21px;
  }
  .holder-title {
    color: var(--brand-blue);
    font-size: 11px;
    margin-top: 1px;
  }

  .contact {
    position: absolute;
    right: 22px;
    top: 128px;
    color: var(--white);
    font-size: 11.5px;
    line-height: 15px;
    text-align: right;
    list-style: none;
  }
  .contact li { display: flex; justify-content: flex-end; align-items: center; gap: 6px; }
  .contact .icon { width: 10px; height: 10px; flex: none; }
  .contact .address { margin-top: 10px; padding-right: 16px; }
</style>
</head>
<body>

<section class="card card-back" aria-label="Card back">
  <div class="back-wordmark">
    <span class="mark-square"></span>
    <span class="company-name">Veldmark Supplies</span>
  </div>
</section>

<section class="card card-front" aria-label="Card front">
  <svg class="front-bands" viewBox="0 0 520 297" width="520" height="297" aria-hidden="true">
    <polygon points="0,180 170,194 520,48 520,297 0,297" fill="var(--brand-blue)"/>
    <polygon points="0,190 172,205 520,60 520,297 0,297" fill="var(--brand-red)"/>
  </svg>

  <div class="front-wordmark">
    <span class="mark-square"></span>
    <span class="company-name">Veldmark Supplies</span>
  </div>

  <div class="holder">
    <div class="holder-name">Daniel Hartwell</div>
    <div class="holder-title">President</div>
  </div>

  <ul class="contact">
    <li>555-201-4837
      <svg class="icon" viewBox="0 0 10 10"><path d="M2 1 L4 1 L4.5 3.5 L3.3 4.3 Q4.5 6.2 5.7 6.7 L6.5 5.5 L9 6 L9 8 Q8.5 9 7 9 Q1 7.5 1 2.5 Q1 1.3 2 1Z" fill="var(--brand-blue)"/></svg>
    </li>
    <li>555-309-6142
      <svg class="icon" viewBox="0 0 10 10"><rect x="2.5" y="0.5" width="5" height="9" rx="1" fill="none" stroke="var(--brand-blue)"/><circle cx="5" cy="8" r="0.6" fill="var(--brand-blue)"/></svg>
    </li>
    <li>info@veldmarksupplies.com
      <svg class="icon" viewBox="0 0 10 10"><rect x="0.5" y="2" width="9" height="6.5" fill="var(--brand-blue)"/><path d="M0.5 2 L5 5.8 L9.5 2" fill="none" stroke="var(--white)" stroke-width="0.8"/></svg>
    </li>
    <li>www.veldmarksupplies.com
      <svg class="icon" viewBox="0 0 10 10"><circle cx="5" cy="5" r="4.5" fill="var(--brand-blue)"/><path d="M0.5 5 H9.5 M5 0.5 Q2.5 5 5 9.5 M5 0.5 Q7.5 5 5 9.5" fill="none" stroke="var(--white)" stroke-width="0.6"/></svg>
    </li>
    <li class="address">412 Alder Street</li>
    <li style="padding-right:16px">Calder Falls, Canada 58210</li>
  </ul>
</section>

</body>
</html>
```